Velmora Freightway Solutions Business cards

Would like a very unique design catchy but professional for business cards. Please use log provided.Marlon WellsCeo and Founder TransCon Logistix Solutions1-888-913-3225mwells@tlsolutionsus.comwww.tlsolutionsus.com

```html
<!DOCTYPE html>
<html lang="en">
<head>
<meta charset="utf-8">
<title>Velmora Freightway Solutions – Business Card</title>
<link href="https://fonts.googleapis.com/css2?family=Josefin+Sans:wght@400;600&display=swap" rel="stylesheet">
<style>
  :root {
    --page-bg: #e8e5e0;
    --card-light: #f4f5f7;
    --card-silver: #d9dde3;
    --navy: #123f86;
    --blue-deep: #174a8e;
    --blue-mid: #2a5fa3;
    --red: #c81f2a;
    --red-dark: #a8161f;
    --ink-light: #eef1f6;
    --ink-soft: #d7e0ee;
  }
  html, body {
    margin: 0;
    width: 1200px;
    height: 970px;
    overflow: hidden;
    background: var(--page-bg);
    font-family: "Josefin Sans", sans-serif;
  }
  .business-card {
    position: absolute;
    left: 80px;
    top: 190px;
    width: 1040px;
    height: 590px;
    border-radius: 22px;
    overflow: hidden;
    background: linear-gradient(180deg, var(--card-light) 0%, var(--card-silver) 100%);
    box-shadow: 0 10px 30px rgba(0,0,0,0.18);
  }
  .card-shapes {
    position: absolute;
    inset: 0;
  }
  .brand-name {
    position: absolute;
    left: 0;
    right: 0;
    top: 92px;
    margin: 0;
    text-align: center;
    color: var(--navy);
    font-weight: 600;
    font-size: 46px;
    line-height: 58px;
    letter-spacing: 1px;
  }
  .holder {
    position: absolute;
    right: 553px;
    top: 410px;
    text-align: right;
    color: var(--ink-light);
  }
  .holder-name {
    font-size: 36px;
    letter-spacing: 1px;
    line-height: 40px;
  }
  .holder-role {
    font-size: 25px;
    letter-spacing: 1px;
    color: var(--ink-soft);
  }
  .divider {
    position: absolute;
    left: 520px;
    top: 395px;
    width: 2px;
    height: 98px;
    background: var(--red);
  }
  .contact-list {
    position: absolute;
    left: 550px;
    top: 390px;
    margin: 0;
    padding: 0;
    list-style: none;
    color: var(--ink-light);
    font-size: 25px;
    letter-spacing: 0.5px;
  }
  .contact-item {
    display: flex;
    align-items: center;
    height: 36px;
  }
  .contact-icon {
    width: 30px;
    height: 30px;
    margin-right: 18px;
    flex: none;
  }
  .footer-band-text {
    position: absolute;
    left: 0;
    right: 0;
    top: 548px;
    text-align: center;
    color: var(--ink-soft);
    font-size: 26px;
    letter-spacing: 6px;
    text-transform: uppercase;
  }
</style>
</head>
<body>
  <div class="business-card">
    <svg class="card-shapes" width="1040" height="590" viewBox="0 0 1040 590" aria-hidden="true">
      <defs>
        <linearGradient id="blueField" x1="0" y1="0" x2="0" y2="1">
          <stop offset="0" stop-color="#2a5fa3"/>
          <stop offset="1" stop-color="#143f7e"/>
        </linearGradient>
        <linearGradient id="redBand" x1="0" y1="0" x2="1" y2="0">
          <stop offset="0" stop-color="#c81f2a"/>
          <stop offset="0.5" stop-color="#a8161f"/>
          <stop offset="1" stop-color="#c81f2a"/>
        </linearGradient>
      </defs>
      <path class="blue-field" d="M0,195 Q520,505 1040,190 L1040,532 L0,532 Z" fill="url(#blueField)"/>
      <path class="accent-curve" d="M0,185 Q520,490 1040,178 L1040,184 Q520,506 0,195 Z" fill="#c81f2a"/>
      <rect class="silver-rule" x="0" y="532" width="1040" height="5" fill="#d9dde3"/>
      <rect class="footer-band" x="0" y="537" width="1040" height="53" fill="url(#redBand)"/>
    </svg>

    <h1 class="brand-name">Velmora Freightway<br>Solutions</h1>

    <div class="holder">
      <div class="holder-name">Dorian Pike</div>
      <div class="holder-role">Ceo and Founder</div>
    </div>

    <div class="divider"></div>

    <ul class="contact-list">
      <li class="contact-item">
        <svg class="contact-icon" viewBox="0 0 30 30" aria-hidden="true">
          <circle cx="15" cy="15" r="13" fill="none" stroke="#d7e0ee" stroke-width="2"/>
          <rect x="10.5" y="8" width="9" height="14" rx="1.5" fill="none" stroke="#d7e0ee" stroke-width="2"/>
        </svg>
        <span>1-888-470-6158</span>
      </li>
      <li class="contact-item">
        <svg class="contact-icon" viewBox="0 0 30 30" aria-hidden="true">
          <circle cx="15" cy="15" r="13" fill="none" stroke="#d7e0ee" stroke-width="2"/>
          <rect x="8.5" y="10" width="13" height="10" fill="none" stroke="#d7e0ee" stroke-width="1.8"/>
          <path d="M8.5,10 L15,16 L21.5,10" fill="none" stroke="#d7e0ee" stroke-width="1.6"/>
        </svg>
        <span>dpike@vfwayroutes.com</span>
      </li>
      <li class="contact-item">
        <svg class="contact-icon" viewBox="0 0 30 30" aria-hidden="true">
          <circle cx="15" cy="15" r="13" fill="none" stroke="#d7e0ee" stroke-width="2"/>
          <circle cx="15" cy="15" r="7.5" fill="none" stroke="#d7e0ee" stroke-width="1.5"/>
          <ellipse cx="15" cy="15" rx="3.2" ry="7.5" fill="none" stroke="#d7e0ee" stroke-width="1.2"/>
          <path d="M7.5,15 H22.5" stroke="#d7e0ee" stroke-width="1.2"/>
        </svg>
        <span>www.vfwayroutes.com</span>
      </li>
    </ul>

    <div class="footer-band-text">Velmora Freightway Solutions</div>
  </div>
</body>
</html>
```